Companybrochure for Consulting & Financing Firm

I need to have a Company Brochure asap for our company. We have a website that describes what we do, but we need also a brochure, that can be sent by PDF of eventually be printed as well.

The brochure should be short but nice and appealing to the customers.

We provide professional management consulting and help our customers to get finance for very diferent projects. Our business has a lot to do with personal relations, but also we are very professional in the way we work and how develop the solutions for our clients. Our clients are mainly government-owned firm, but also private trading companies and wealthy private investors.

Our customers are mainly in Latin America, but the company is headquater is in Switzerland. We are opening offices in Panama and Caracas, this should be easaly be adabtable later.

Please have a look at our website www.vorelpartners.ch. In the brochure, we would segment our services in 1.) Project Developments 2.) Management Conulting 3.) Investment Management and 4.) Finance Solutions.

Also do have a look at www.vorelpartners.ch
(Click E for the English version)
Updates

I managed to put the Mock-Up to the Website.
It is actually not really a mock-up, it is a version I have designed myself.
Well as I am not a designer, I hope you can make it much better.
The content however is what I would put in any other design as well.

Target Market(s)

Top Management, Investors, Entrepreneurs, Government Officials

Industry/Entity Type

Management Consulting

Requirements
Must have
• Design should reflect this image elements:

We are entrepreneurs.
We are comitted to get things done.
We work closely with the client side by side.
We are a professional partner.
We are not afraid of delivering unconventional solutions.
We look at the problem from various angles.
We analyse, develop solutions and implent results.
Should not have
• Typical US-American style elements. We do not want to give the impression of being a US company.

We do not want to appear to be neo-liberal. We are a politically neutral professional consulting firm.

```html
<!DOCTYPE html>
<html lang="en">
<head>
<meta charset="utf-8">
<title>Vorel Partners AG – Brochure</title>
<link rel="stylesheet" href="https://fonts.googleapis.com/css2?family=Oswald:wght@500;600&family=Source+Sans+3:wght@400;600;700&display=swap">
<style>
  :root {
    --navy: #27235f;
    --charcoal: #333333;
    --logo-grey: #3a3a3a;
    --paper: #ffffff;
    --backdrop: #e9e7e3;
    --white: #ffffff;
    --sky: #a9c6e2;
    --concrete: #d9d2c2;
    --steel: #6b6760;
  }
  * { margin: 0; padding: 0; box-sizing: border-box; }
  html, body {
    width: 1200px; height: 960px; overflow: hidden;
    background: var(--backdrop);
  }
  .spread {
    position: absolute; left: 45px; top: 98px;
    width: 1180px; height: 812px;
    transform: scale(0.94); transform-origin: 0 0;
  }
  .page {
    position: absolute; top: 0; width: 575px; height: 812px;
    background: var(--paper);
    box-shadow: 0 2px 10px rgba(0,0,0,0.18);
  }
  .page--back { left: 0; }
  .page--front { left: 605px; }

  .condensed { font-family: "Oswald", "Arial Narrow", sans-serif; }
  .sans { font-family: "Source Sans 3", "Helvetica Neue", Arial, sans-serif; }

  /* Back page */
  .values {
    position: absolute; left: 203px; top: 207px; width: 372px; height: 388px;
    background: var(--navy); color: var(--white);
    clip-path: polygon(94px 0, 100% 0, 100% 308px, 294px 100%, 0 100%, 0 83px);
    padding: 88px 10px 0 12px;
  }
  .values__title {
    font-family: "Oswald", "Arial Narrow", sans-serif; font-weight: 500;
    font-size: 27px; letter-spacing: 0.2px; line-height: 1; margin-left: 3px;
    margin-bottom: 18px; transform: scaleX(0.88); transform-origin: left;
    white-space: nowrap;
  }
  .values__list { list-style: none; font-family: "Source Sans 3", Arial, sans-serif; font-weight: 600; font-size: 15.5px; line-height: 15px; }
  .values__list li { padding-left: 14px; text-indent: -14px; margin-bottom: 12px; }
  .values__list li::before { content: "> "; }

  .contact {
    position: absolute; left: 0; top: 385px; width: 186px; height: 193px;
    background: var(--charcoal); color: var(--white);
    clip-path: polygon(0 0, 100% 0, 100% 155px, 148px 100%, 0 100%);
    padding: 41px 0 0 25px;
    font-family: "Source Sans 3", Arial, sans-serif; font-size: 12.5px; font-weight: 600; line-height: 14.5px;
  }
  .contact p + p { margin-top: 10px; }

  .registered {
    position: absolute; left: 72px; top: 590px; width: 114px; height: 119px;
    background: var(--navy); color: var(--white);
    clip-path: polygon(0 0, 100% 0, 100% 95px, 92px 100%, 0 100%);
    padding-top: 22px; text-align: center;
    font-family: "Oswald", "Arial Narrow", sans-serif; font-weight: 500; font-size: 13px; line-height: 16.5px;
  }
  .wordmark { font-family: "Source Sans 3", Arial, sans-serif; font-weight: 600; color: var(--logo-grey); white-space: nowrap; }
  .wordmark--back { position: absolute; left: 205px; top: 600px; font-size: 25px; }

  /* Front page */
  .cover-photo {
    position: absolute; left: 29px; top: 0; width: 516px; height: 776px;
    background: linear-gradient(180deg, var(--sky) 0%, #c9d6df 22%, var(--concrete) 38%, #a39c8e 55%, var(--steel) 80%, #57534d 100%);
    clip-path: polygon(0 0, 100% 0, 100% 715px, 455px 100%, 0 100%);
  }
  .cover-band {
    position: absolute; left: 140px; top: 30px; width: 405px; height: 52px;
    background: rgba(200, 220, 238, 0.55);
  }
  .wordmark--front { position: absolute; left: 141px; top: 30px; font-size: 39px; line-height: 52px; }

  .services {
    position: absolute; left: 186px; top: 498px; width: 244px; height: 254px;
    background: var(--navy); color: var(--white);
    clip-path: polygon(38px 0, 100% 0, 100% 100%, 0 100%, 0 38px);
    padding: 62px 0 0 21px;
  }
  .services__intro {
    font-family: "Oswald", "Arial Narrow", sans-serif; font-weight: 500;
    font-size: 18px; line-height: 19.5px; width: 250px;
    transform: scaleX(0.86); transform-origin: left; margin-bottom: 14px;
  }
  .services__list { list-style: none; font-family: "Source Sans 3", Arial, sans-serif; font-size: 16.5px; line-height: 21px; }
  .services__list li::before { content: "> "; }

  .motto {
    position: absolute; left: 60px; top: 630px; width: 120px; height: 120px;
    background: var(--charcoal); color: var(--white);
    display: flex; align-items: center; justify-content: center; text-align: center;
    font-family: "Oswald", "Arial Narrow", sans-serif; font-weight: 500; font-size: 27px; line-height: 31px;
  }
  .motto span { display: block; transform: scaleX(0.85); }
</style>
</head>
<body>
<main class="spread">
  <section class="page page--back">
    <div class="values">
      <h2 class="values__title">ANALYZE &#8226; DEVELOP &#8226; DELIVER</h2>
      <ul class="values__list">
        <li>We are entrepreneurs.</li>
        <li>We are comitted to get things done.</li>
        <li>We work closely with the client side by side.</li>
        <li>We are a professional partner.</li>
        <li>We are not afraid of delivering unconventional solutions.</li>
        <li>We look at the problem from various angles</li>
        <li>We analyse, develop solutions and implent results.</li>
      </ul>
    </div>
    <address class="contact" style="font-style:normal">
      <p>Vorel Partners AG<br>Lindenhof-Weg 14<br>CH-8045 Zürich</p>
      <p>Tel.&nbsp; +41 44 210 55 40<br>Fax. +41 44 210 55 49</p>
      <p>www.vorelpartners.ch<br>info@vorelpartners.ch</p>
    </address>
    <div class="registered">Vorel Partners<br>AG is registered<br>as a Swiss stock<br>corporation<br>since 1995.</div>
    <div class="wordmark wordmark--back">Vorel Partners AG</div>
  </section>

  <section class="page page--front">
    <div class="cover-photo" role="img" aria-label="Photograph of a construction site with steel reinforcement bars in the foreground and concrete walls under a blue sky"></div>
    <div class="cover-band"></div>
    <h1 class="wordmark wordmark--front">Vorel Partners AG</h1>
    <div class="services">
      <p class="services__intro">We are a professional consulting, financing and investment firm operating in the fields of:</p>
      <ul class="services__list">
        <li>Project Development</li>
        <li>Management Consulting</li>
        <li>Investment Management</li>
        <li>Finance Solutions</li>
      </ul>
    </div>
    <div class="motto"><span>ANALYZE<br>DEVELOP<br>DELIVER</span></div>
  </section>
</main>
</body>
</html>
```